Black Car Limousine transportation business in Naples Florida

Always stand for my reliability and RVD stands for Love, K and M are the first initials of my children's names. It should show professionalism and a dedication to customer service. We keep our clients identities private. Show our professionalism. We are Black car Black tie company. We service transportation on a reserve basis to and from residents, airports, casinos, hotels,

Target Market(s)

It is a Private car service. High end clients. Businesses, Celebrity and athletes. Service to airports, hotels, special events.

Industry/Entity Type

Business

Contact Information for Business Card

A pearl metallic or Luster card. Standard business card size. Would like the name, Company email, show we take credit cards and phone number. Currently I don't have a website but will like to add later.

Logo Text

STEADFAST RVD TRANSPORTATION

Font styles to use
Serif

Colors
eaeaea
000000

Requirements
Must have
• Must have Company email, show we take credit cards and phone number. Currently I don't have a website but will like to add later.
Nice to have
• Would like to stay with a black and white theme. Open to some color trim.
Should not have
• Open to suggestions

```html
<!DOCTYPE html>
<html lang="en">
<head>
<meta charset="utf-8">
<title>Steadfast RVD Transportation – Business Card</title>
<link rel="stylesheet" href="https://fonts.googleapis.com/css2?family=Crimson+Text:wght@400;600;700&display=swap">
<style>
  :root {
    --backdrop: #e4e2df;
    --pearl-light: #f4f4f3;
    --pearl: #eaeaea;
    --pearl-dark: #d9d9d8;
    --ink: #000000;
    --black-card-light: #262626;
    --black-card: #000000;
    --trim: #eaeaea;
  }
  html, body {
    margin: 0;
    padding: 0;
    width: 1200px;
    height: 900px;
    overflow: hidden;
    background: var(--backdrop);
  }
  .canvas {
    position: relative;
    width: 1200px;
    height: 900px;
    font-family: "Crimson Text", Georgia, serif;
  }
  .card {
    position: absolute;
    box-shadow: 0 6px 18px rgba(0, 0, 0, 0.2);
  }
  .card-front {
    left: 238px;
    top: 62px;
    width: 555px;
    height: 342px;
    background: radial-gradient(ellipse at 50% 30%, var(--pearl-light), var(--pearl) 60%, var(--pearl-dark));
    color: var(--ink);
    text-align: center;
  }
  .contact-block {
    position: absolute;
    left: 0;
    right: 0;
    top: 84px;
    font-size: 16px;
    line-height: 20px;
  }
  .contact-name {
    font-size: 20px;
    font-weight: 700;
    line-height: 24px;
  }
  .contact-title { margin-bottom: 16px; }
  .contact-lines { margin-bottom: 6px; }
  .card-payments {
    display: flex;
    justify-content: center;
    align-items: center;
    gap: 6px;
    height: 20px;
    margin-bottom: 16px;
    font-size: 14px;
  }
  .card-payments svg { display: block; }
  .card-back {
    left: 459px;
    top: 518px;
    width: 559px;
    height: 342px;
    background: radial-gradient(ellipse at 30% 20%, var(--black-card-light), var(--black-card) 70%);
  }
  .brand-name {
    position: absolute;
    left: 0;
    right: 0;
    top: 96px;
    text-align: center;
    color: var(--trim);
    font-weight: 400;
    letter-spacing: 1px;
  }
  .brand-top { font-size: 30px; line-height: 36px; letter-spacing: 4px; }
  .brand-main { font-size: 78px; line-height: 78px; letter-spacing: 6px; }
  .brand-bottom { font-size: 30px; line-height: 40px; letter-spacing: 2px; }
</style>
</head>
<body>
<main class="canvas">
  <section class="card card-front" aria-label="Business card front">
    <div class="contact-block">
      <div class="contact-name">Daniel Harper</div>
      <div class="contact-title">Managing Director</div>
      <div class="contact-lines">
        044-555 010 246<br>
        info@rvdcars.com
      </div>
      <div class="card-payments">
        <svg width="26" height="18" viewBox="0 0 26 18" role="img" aria-label="Credit card">
          <rect x="1" y="1" width="24" height="16" rx="2.5" fill="none" stroke="#000" stroke-width="1.4"/>
          <rect x="1" y="5" width="24" height="3" fill="#000"/>
          <rect x="4" y="11" width="7" height="2" fill="#000"/>
        </svg>
        <span>Major credit cards accepted</span>
      </div>
      <div class="contact-address">
        12345, Address Goes Here<br>
        Country Name, 123456.
      </div>
    </div>
  </section>

  <section class="card card-back" aria-label="Business card back">
    <div class="brand-name">
      <div class="brand-top">STEADFAST</div>
      <div class="brand-main">RVD</div>
      <div class="brand-bottom">TRANSPORTATION</div>
    </div>
  </section>
</main>
</body>
</html>
```